Erotik Online Shop
Zielgruppe
Kunden des Online Shops, vorzugsweise schwule Männer wobei der Shop auch die hetero Ziegruppe bedienen bzw. befriedigen kann.
Aufgabenstellung
Für den Relounch unserers Online Shops benötigen wir mehrer Grafiken für die Startseite des Shops sowie eventuell einen Überabreitung unseres Logos.

```html
<!DOCTYPE html>
<html lang="de">
<head>
<meta charset="utf-8">
<title>Pluvo24 – Startseiten-Grafiken</title>
<link href="https://fonts.googleapis.com/css2?family=Bebas+Neue&family=Oswald:wght@500;700&display=swap" rel="stylesheet">
<style>
  :root{
    --red:#d3121b;
    --red-dark:#9e0b12;
    --black:#111111;
    --ink:#1a1a1a;
    --white:#ffffff;
    --line:#dedede;
    --panel:#2a2a2a;
    --panel-dark:#161616;
    --green:#3cbf1f;
    --photo-grey-a:#c4c4c4;
    --photo-grey-b:#8a8a8a;
    --photo-warm-a:#cdbcb1;
    --photo-warm-b:#b3a398;
  }
  *{box-sizing:border-box;margin:0;padding:0}
  html,body{width:1200px;height:1200px;overflow:hidden;background:var(--white)}
  body{position:relative;font-family:"Bebas Neue","Oswald",sans-serif;color:var(--ink)}

  .banner{position:absolute;left:46px;width:599px;height:311px;background:var(--white);
    border:1px solid var(--line);border-radius:8px;overflow:hidden}
  .banner--toys{top:36px}
  .banner--workouts{top:372px}
  .banner--diy{top:721px}

  .photo{position:absolute;top:0;bottom:0}
  .banner--toys .photo{left:330px;width:250px;
    background:linear-gradient(135deg,var(--photo-grey-a),var(--photo-grey-b))}
  .banner--workouts .photo{left:40px;width:200px;
    background:linear-gradient(135deg,var(--photo-warm-a),var(--photo-warm-b))}
  .banner--diy .photo{left:40px;width:210px;bottom:auto;height:250px;
    background:linear-gradient(135deg,var(--photo-warm-a),var(--photo-warm-b))}

  .tag{display:inline-block;background:var(--black);color:var(--white);line-height:1;padding:4px 10px 0}
  .tag .hot,.red{color:var(--red)}

  .toys-head{position:absolute;left:38px;top:40px}
  .toys-head .tag{display:block;width:max-content}
  .toys-head .l1{font-size:50px}
  .toys-head .l2{font-size:60px;margin-left:36px}
  .toys-head .small{font-size:40px}
  .and-girls{position:absolute;left:262px;top:178px;font-family:"Oswald",sans-serif;font-weight:500;font-size:12px;letter-spacing:.5px}
  .banner-foot{position:absolute;bottom:14px;font-size:30px;line-height:1;letter-spacing:.5px;color:var(--black)}
  .banner--toys .banner-foot{left:14px}

  .workouts-head{position:absolute;left:255px;top:64px}
  .workouts-head .kicker{font-size:22px;display:block;margin-left:2px}
  .workouts-head .tag{display:block;width:max-content;font-size:62px;color:var(--red)}
  .banner--workouts .banner-foot{right:22px}

  .diy-head{position:absolute;left:262px;top:60px}
  .diy-head .tag{display:block;width:max-content;font-size:62px}
  .diy-head .tag.yourself{color:var(--red);margin-left:72px;margin-top:6px}
  .diy-head .sub{display:block;font-size:20px;margin:10px 0 0 150px}
  .banner--diy .banner-foot{right:22px;font-size:29px}

  .brand{position:absolute;color:var(--red);font-family:"Bebas Neue",sans-serif;line-height:1;letter-spacing:2px}
  .brand--hero{left:723px;top:110px;width:405px;text-align:center;font-size:124px}
  .brand--foot-left{left:68px;top:1110px;font-size:60px}
  .brand--foot-right{left:900px;top:1110px;font-size:60px}

  .safer{position:absolute;left:732px;top:393px;width:399px;height:249px;border-radius:4px;overflow:hidden;
    background:linear-gradient(90deg,#3a3a3a 0%,#262626 40%,#1c1c1c 100%)}
  .safer .photo{left:0;width:140px;background:linear-gradient(90deg,#5a5a5a,#2a2a2a)}
  .safer-kicker{position:absolute;right:24px;top:14px;color:var(--white);font-size:28px}
  .safer-title{position:absolute;right:16px;top:50px;background:var(--white);border:2px solid var(--red);
    color:var(--red);font-size:44px;line-height:1;padding:4px 14px 0;font-weight:400}
  .safer-list{position:absolute;right:18px;top:112px;list-style:none;color:var(--white);font-size:21px;line-height:25px;text-align:right}
  .safer-list li{display:flex;justify-content:flex-end;align-items:center;gap:10px}
  .tick{width:20px;height:18px;flex:none}

  .tile{position:absolute;top:745px;height:262px;border-radius:4px;overflow:hidden;
    background:linear-gradient(180deg,var(--panel) 0%,var(--panel-dark) 100%);color:var(--white);text-align:center}
  .tile--pay{left:717px;width:138px}
  .tile--news{left:871px;width:136px}
  .tile--partner{left:1024px;width:136px}

  .pay-head{font-size:24px;line-height:1;margin-top:6px}
  .pay-head .red{display:block}
  .pay-badges{list-style:none;margin-top:14px;display:flex;flex-direction:column;align-items:center;gap:12px}
  .pay-badges li{width:54px;height:32px;border-radius:4px;background:linear-gradient(180deg,#ffffff,#d6d6d6)}

  .news-head{font-size:50px;line-height:.9;margin-top:10px}
  .news-free{font-size:18px;letter-spacing:2px;margin-top:4px}
  .news-field{display:block;margin:0 auto;width:118px;height:24px;background:var(--white);color:#444;
    font-family:"Oswald",sans-serif;font-size:11px;text-align:left;padding:4px 6px;border-radius:2px}
  .news-field:first-of-type{margin-top:44px}
  .news-field + .news-field{margin-top:6px}
  .news-btn{display:block;margin:10px auto 0;width:118px;height:24px;background:var(--red);border-radius:3px;
    font-family:"Oswald",sans-serif;font-weight:700;font-size:12px;line-height:24px}

  .partner-head{background:var(--red-dark);font-size:32px;line-height:.9;padding:6px 0 4px}
  .partner-photo{height:66px;background:linear-gradient(180deg,#6e6e6e,#3a3a3a)}
  .partner-step{display:block;margin:8px auto 0;width:122px;border:1px solid var(--white);background:var(--black);
    font-size:19px;line-height:24px}
  .partner-step--money{color:var(--red)}

  .foot-band{position:absolute;left:0;top:1074px;width:1200px;height:126px;background:var(--black)}
</style>
</head>
<body>

<section class="banner banner--toys">
  <div class="photo" role="img" aria-label="Schwarz-weiß Foto eines muskulösen Mannes in Boxershorts"></div>
  <div class="toys-head">
    <span class="tag l1"><span class="hot">Hot</span> Toys</span>
    <span class="tag l2"><span class="small">for </span><span class="hot">Hot</span> Boys</span>
  </div>
  <span class="and-girls">(AND GIRLS)</span>
  <p class="banner-foot">Come and get them. <span class="red">Now!</span></p>
</section>

<section class="banner banner--workouts">
  <div class="photo" role="img" aria-label="Foto eines trainierten Mannes mit Kopfhörern in Sporthose"></div>
  <div class="workouts-head">
    <span class="kicker">Hot stuff for your</span>
    <span class="tag">Private</span>
    <span class="tag">Workouts</span>
  </div>
  <p class="banner-foot">Alles andere ist nur <span class="red">Spielzeug!</span></p>
</section>

<section class="banner banner--diy">
  <div class="photo" role="img" aria-label="Foto eines langhaarigen Mannes mit zurückgelegtem Kopf"></div>
  <div class="diy-head">
    <span class="tag">Do it</span>
    <span class="tag yourself">Yourself</span>
    <span class="sub">Selbst ist der Mann!</span>
  </div>
  <p class="banner-foot">Hol dir das Zeug für echte Handwerker</p>
</section>

<div class="brand brand--hero">Pluvo24</div>

<section class="safer">
  <div class="photo" role="img" aria-label="Dunkles Foto eines männlichen Oberkörpers"></div>
  <p class="safer-kicker">Bei uns nie ohne...</p>
  <h2 class="safer-title">Safer Shopping</h2>
  <ul class="safer-list">
    <li>Geld-zurück Garantie<svg class="tick" viewBox="0 0 20 18"><path d="M2 9 L8 15 L18 2" fill="none" stroke="var(--green)" stroke-width="4"/></svg></li>
    <li>Diskrete Verpackung<svg class="tick" viewBox="0 0 20 18"><path d="M2 9 L8 15 L18 2" fill="none" stroke="var(--green)" stroke-width="4"/></svg></li>
    <li>Kein Mindestbestellwert<svg class="tick" viewBox="0 0 20 18"><path d="M2 9 L8 15 L18 2" fill="none" stroke="var(--green)" stroke-width="4"/></svg></li>
    <li>Faire &amp; günstige Versandkosten<svg class="tick" viewBox="0 0 20 18"><path d="M2 9 L8 15 L18 2" fill="none" stroke="var(--green)" stroke-width="4"/></svg></li>
    <li>Onlineshopping seit 1999!<svg class="tick" viewBox="0 0 20 18"><path d="M2 9 L8 15 L18 2" fill="none" stroke="var(--green)" stroke-width="4"/></svg></li>
  </ul>
</section>

<section class="tile tile--pay">
  <p class="pay-head"><span class="red">100% sicher</span>zahlen mit:</p>
  <ul class="pay-badges" aria-label="Zahlungsarten">
    <li></li><li></li><li></li><li></li>
  </ul>
</section>

<section class="tile tile--news">
  <p class="news-head">News<br><span class="red">Letter</span></p>
  <p class="news-free">100% Free</p>
  <span class="news-field">Name</span>
  <span class="news-field">email Adresse</span>
  <span class="news-btn">REGISTER NOW</span>
</section>

<section class="tile tile--partner">
  <p class="partner-head">Partner<br>Programm</p>
  <div class="partner-photo" role="img" aria-label="Foto eines männlichen Oberkörpers"></div>
  <span class="partner-step">Unser Banner</span>
  <span class="partner-step">Deine Homepage</span>
  <span class="partner-step partner-step--money">$ Dein Geld $</span>
</section>

<footer class="foot-band"></footer>
<div class="brand brand--foot-left">Pluvo24</div>
<div class="brand brand--foot-right">Pluvo24</div>

</body>
</html>
```